General contractor/GM consaltant business card

I need a card for my contracting company in North Dakota, we build industrial buildings for the oil feild and oil feild related companies offices, shops, airplain hangars, airports ext. We have a familly atmosphere on the job and are very relational and personal.
Industry/Entity Type
Industrial
Contact Information for Business Card
Ridgepost Contractors LLC.
Derek T.Holloway
4837 Tamarind dr. Colorado Springs, CO. 80917
Cell# 406-555-0148
derek@ridgepostcontractors.com

```html
<!DOCTYPE html>
<html lang="en">
<head>
<meta charset="utf-8">
<title>Ridgepost Contractors LLC. – Business Card</title>
<link href="https://fonts.googleapis.com/css2?family=Tinos:wght@400;700&display=swap" rel="stylesheet">
<style>
  :root {
    --backdrop: #ecebe8;
    --paper: #ffffff;
    --brand-red: #e2253a;
    --brand-blue: #1d4f9c;
    --ink: #1b1b1b;
    --light: #ffffff;
  }
  * { box-sizing: border-box; margin: 0; padding: 0; }
  html, body {
    width: 1200px; height: 858px; overflow: hidden;
    background: var(--backdrop);
    font-family: "Tinos", "Times New Roman", serif;
  }
  .canvas {
    width: 1200px; height: 858px;
    display: flex; flex-direction: column;
    align-items: center; justify-content: center; gap: 34px;
  }
  .card {
    position: relative;
    width: 660px; height: 377px;
    background: var(--paper);
    box-shadow: 0 4px 14px rgba(0,0,0,.14);
    overflow: hidden;
  }
  .wordmark { white-space: nowrap; }

  /* Front */
  .front .wordmark {
    position: absolute; left: 56px; top: 92px;
    display: flex; align-items: center; gap: 14px;
    font-weight: 700; font-size: 38px; color: var(--brand-red);
  }
  .wordmark .mark-square {
    flex: none; width: 22px; height: 22px; background: var(--brand-blue);
  }
  .front .contact {
    position: absolute; right: 40px; top: 176px;
    text-align: right; font-size: 16px; line-height: 1.35; color: var(--ink);
    list-style: none;
  }
  .contact li { display: flex; justify-content: flex-end; align-items: flex-start; gap: 10px; }
  .contact svg { flex: none; margin-top: 3px; }
  .front .band {
    position: absolute; left: 0; right: 0; bottom: 0; height: 74px;
  }
  .band .band-shape { position: absolute; inset: 0; }
  .band .holder-name {
    position: absolute; left: 34px; bottom: 22px;
    font-size: 22px; color: var(--light);
  }
  .band .email {
    position: absolute; right: 36px; bottom: 22px;
    display: flex; align-items: center; gap: 10px;
    font-size: 17px; color: var(--light);
  }
  .band .email svg { flex: none; }

  /* Back */
  .back .wordmark {
    position: absolute; left: 56px; top: 150px;
    display: flex; align-items: center; gap: 16px;
    font-weight: 700; font-size: 42px; line-height: 1; color: var(--brand-red);
  }
  .back .wordmark .mark-square { width: 26px; height: 26px; }
  .back .rule {
    position: absolute; left: 0; height: 3px;
  }
  .back .rule-red { top: 212px; width: 600px; background: var(--brand-red); }
  .back .rule-blue { top: 222px; width: 608px; background: var(--brand-blue); }
</style>
</head>
<body>
<main class="canvas">

  <section class="card front" aria-label="Card front">
    <div class="wordmark"><span class="mark-square"></span>Ridgepost Contractors LLC.</div>

    <ul class="contact">
      <li>406-555-0148
        <svg width="12" height="14" viewBox="0 0 12 14" aria-hidden="true"><rect x="1" y="0.5" width="10" height="13" rx="2" fill="none" stroke="var(--brand-blue)" stroke-width="1.4"/><rect x="3" y="2.5" width="6" height="7" fill="var(--brand-blue)"/></svg>
      </li>
      <li>4837 Tamarind dr. Colorado Springs,<br>CO. 80917
        <svg width="12" height="14" viewBox="0 0 12 14" aria-hidden="true"><path d="M6 13.5C2.5 9 1 7 1 5a5 5 0 0 1 10 0c0 2-1.5 4-5 8.5z" fill="var(--brand-blue)"/><circle cx="6" cy="5" r="1.8" fill="#fff"/></svg>
      </li>
    </ul>

    <div class="band">
      <svg class="band-shape" width="660" height="74" viewBox="0 0 660 74" aria-hidden="true">
        <polygon points="0,0 330,0 330,74 0,74" fill="var(--brand-red)"/>
        <path d="M318,74 L318,22 Q318,8 334,8 L660,8 L660,74 Z" fill="var(--brand-blue)"/>
        <path d="M328,8 Q330,0 340,0 L660,0 L660,4 L342,4 Q334,4 330,8 Z" fill="var(--brand-red)"/>
      </svg>
      <span class="holder-name">Derek T.Holloway</span>
      <span class="email">derek@ridgepostcontractors.com
        <svg width="14" height="10" viewBox="0 0 14 10" aria-hidden="true"><rect x="0.5" y="0.5" width="13" height="9" fill="#fff"/><path d="M0.5 0.5L7 6 13.5 0.5" fill="none" stroke="var(--brand-blue)" stroke-width="1.2"/></svg>
      </span>
    </div>
  </section>

  <section class="card back" aria-label="Card back">
    <div class="wordmark"><span class="mark-square"></span>Ridgepost Contractors LLC.</div>
    <div class="rule rule-red"></div>
    <div class="rule rule-blue"></div>
  </section>

</main>
</body>
</html>
```